Im open to ideas.. I was thinking on my business cards aswell as my logo. a place for my name. email. phone number and abn..

ive attched a file with my business logo. which i dont love the colours.. i was think a dark background with charcoal letters so something along those colour schumes but im open to ideas..

BRM Constructions

```html
<!DOCTYPE html>
<html lang="en">
<head>
<meta charset="utf-8">
<title>BRM Constructions – Business Card</title>
<link rel="stylesheet" href="https://fonts.googleapis.com/css2?family=Lato:wght@400;700;900&display=swap">
<style>
  :root {
    --backdrop: #1b1b1b;
    --card-white: #f4f4f4;
    --charcoal: #262626;
    --ink: #1e1e1e;
    --brand-red: #d4221f;
    --red-deep: #a81614;
    --name-grey: #c4c4c4;
    --muted-grey: #9a9a9a;
    --contact-grey: #e2e2e2;
  }
  * { box-sizing: border-box; margin: 0; padding: 0; }
  html, body {
    width: 1200px;
    height: 873px;
    overflow: hidden;
    background: var(--backdrop);
    font-family: "Lato", sans-serif;
  }
  .canvas {
    position: relative;
    width: 1200px;
    height: 873px;
  }
  .business-card {
    position: absolute;
    left: 180px;
    top: 196px;
    width: 840px;
    height: 480px;
    overflow: hidden;
    box-shadow: 0 18px 40px rgba(0, 0, 0, 0.6);
  }
  .card-art {
    position: absolute;
    inset: 0;
    width: 100%;
    height: 100%;
  }
  .wordmark {
    position: absolute;
    left: 150px;
    top: 96px;
    font-weight: 900;
    font-size: 38px;
    line-height: 1;
    letter-spacing: 1px;
    color: var(--ink);
    display: flex;
    align-items: center;
    gap: 12px;
    white-space: nowrap;
  }
  .wordmark-square {
    width: 20px;
    height: 20px;
    background: var(--brand-red);
  }
  .owner {
    position: absolute;
    right: 62px;
    top: 246px;
    text-align: right;
  }
  .owner-name {
    font-weight: 700;
    font-size: 24px;
    color: var(--name-grey);
  }
  .owner-role {
    font-size: 16px;
    color: var(--muted-grey);
    margin-top: 2px;
  }
  .contact-list {
    position: absolute;
    left: 92px;
    top: 338px;
    list-style: none;
  }
  .contact-item {
    display: flex;
    align-items: center;
    gap: 10px;
    font-size: 18px;
    color: var(--contact-grey);
    margin-bottom: 12px;
  }
  .contact-icon {
    width: 26px;
    height: 26px;
    flex: none;
  }
  .website {
    font-weight: 900;
    font-size: 21px;
    color: var(--brand-red);
    margin-top: 6px;
  }
</style>
</head>
<body>
<main class="canvas">
  <section class="business-card">
    <svg class="card-art" viewBox="0 0 840 480" aria-hidden="true">
      <rect class="card-face" width="840" height="480" fill="var(--card-white)"/>
      <path class="red-swoosh" fill="var(--brand-red)"
        d="M0,262 C200,225 420,232 560,168 C680,112 780,98 840,80 L840,110 C780,128 680,146 560,204 C420,270 200,268 0,306 Z"/>
      <path class="red-swoosh-shade" fill="var(--red-deep)"
        d="M0,294 C200,258 420,262 560,194 C680,136 780,118 840,102 L840,110 C780,128 680,146 560,204 C420,270 200,268 0,306 Z"/>
      <path class="charcoal-base" fill="var(--charcoal)"
        d="M0,306 C200,268 420,270 560,204 C680,146 780,128 840,110 L840,480 L0,480 Z"/>
    </svg>

    <div class="wordmark">
      <span class="wordmark-square"></span>
      <span class="wordmark-name">BRM Constructions</span>
    </div>

    <div class="owner">
      <p class="owner-name">Daniel Marsh</p>
      <p class="owner-role">Owner / Founder</p>
    </div>

    <ul class="contact-list">
      <li class="contact-item">
        <svg class="contact-icon" viewBox="0 0 26 26" aria-label="Phone">
          <circle cx="13" cy="13" r="13" fill="var(--brand-red)"/>
          <path d="M9 7.5c.6-.4 1.3-.3 1.7.3l1.1 1.8c.3.5.2 1.1-.2 1.5l-.8.7c.7 1.5 1.8 2.6 3.3 3.3l.7-.8c.4-.4 1-.5 1.5-.2l1.8 1.1c.6.4.7 1.1.3 1.7l-.7.9c-.6.8-1.7 1-2.6.6-3.2-1.4-5.6-3.8-7-7-.4-.9-.2-2 .6-2.6z" fill="#fff"/>
        </svg>
        <span>0412558904</span>
      </li>
      <li class="contact-item">
        <svg class="contact-icon" viewBox="0 0 26 26" aria-label="Email">
          <circle cx="13" cy="13" r="13" fill="var(--brand-red)"/>
          <rect x="7" y="9" width="12" height="8.5" rx="1" fill="#fff"/>
          <path d="M7.5 9.5 13 14l5.5-4.5" fill="none" stroke="var(--brand-red)" stroke-width="1.2"/>
        </svg>
        <span>info@brmconstructions.com</span>
      </li>
      <li class="website">www.brmconstructions.com</li>
    </ul>
  </section>
</main>
</body>
</html>
```